NexaBRIDGE new era @ Hyper Digitalization

We need a Brochure that show all our product, services and consulting related to Hyper Digitalization into the industrial internet of things world.
We need a document that can be handled as a electronic brochure, this means that we need to show strong corporate presence, with strong skill of technology, and we have credentials and key sucess projects related to Manufacturing industries.
Key industries that we attend: Automotive, Chemical, Food and Beverage, Mining, Paper and Pulp, Oil and Gas, Energy Management.
We save money to our customer in 6 ways: 1) Eficiency in operation 2) Production Control 3) Hyper Digitalization of Thing Optimizing asset ussage 4) Maintenance and predictive of assets risks 5) Quality Control reducing Cost 6) Augmented Reality in operation and control
Target Market(s)
Manufacturing Industry. CEO of companies that has challenges of saving operation costs into plants of manufacturing.
Industry/Entity Type
Software
Other font styles liked:
- MONTSERRAT
Requirements
Must have
- Technology Enviroment, our logo, our expertise, simple message about what our company does and the DNA, infography of the company, cases of sucess, cases of savings $ using our tecnology and services, what we can do for the customer in a few words
Nice to have
- standarize our colors related to our presentation, futuristic, information related to Artificial Inteligence related to machinery
Should not have
- old version of technology,

```html
<!DOCTYPE html>
<html lang="en">
<head>
<meta charset="utf-8">
<title>NexaBRIDGE – Hyper Digitalization Brochure</title>
<link href="https://fonts.googleapis.com/css2?family=Montserrat:wght@300;400;500;600;700&display=swap" rel="stylesheet">
<style>
  :root{
    --stage:#9c9c9c;
    --lime:#99ff00;
    --sky:#4fcdf3;
    --page-blue:#6aa3ea;
    --page-blue-light:#7eb2f1;
    --deep-blue:#1f6fe0;
    --night-blue:#0f2a7a;
    --navy-text:#0d1b2e;
    --brand-blue:#2f8ae6;
    --white:#ffffff;
  }
  *{box-sizing:border-box;margin:0;padding:0}
  html,body{width:960px;height:1200px;overflow:hidden}
  body{
    background:radial-gradient(circle at 50% 45%,#b4b4b4 0%,var(--stage) 70%);
    font-family:"Montserrat",sans-serif;color:var(--white);position:relative;
  }
  .page{position:absolute;width:256px;height:360px;overflow:hidden;
    background:linear-gradient(160deg,var(--page-blue) 0%,var(--page-blue-light) 100%);
    box-shadow:4px 6px 10px rgba(0,0,0,.35)}
  .page--cover{left:84px;top:54px;background:var(--sky)}
  .page--expertise{left:358px;top:53px}
  .page--about{left:626px;top:53px}
  .page--dna{left:75px;top:429px}
  .page--partners{left:354px;top:431px}
  .page--savings{left:626px;top:429px}
  .page--offer{left:354px;top:803px}
  .layer{position:absolute;left:0;top:0;width:256px;height:360px}
  .brand{position:absolute;left:18px;top:18px;font-size:9px;font-weight:400;color:var(--brand-blue);letter-spacing:.2px}
  .brand--cover{left:122px;top:240px;color:var(--deep-blue)}
  .photo{position:absolute}

  /* cover */
  .cover-title{position:absolute;left:53px;top:272px;font-size:21px;font-weight:700;line-height:1.15;color:var(--navy-text)}

  /* headings */
  .heading{position:absolute;left:12px;font-weight:400;color:var(--navy-text);line-height:1}
  .heading::after{content:"";display:block;width:55px;height:3px;background:var(--lime);margin-top:2px}
  .subheading{position:absolute;left:12px;font-size:12.5px;font-weight:500;color:var(--white)}
  .copy{position:absolute;left:12px;font-size:8.2px;font-weight:300;line-height:1.22}
  .copy p+p{margin-top:8px}

  /* expertise columns */
  .col{position:absolute;top:208px;font-size:6.3px;font-weight:300;line-height:1.25}
  .col h4{font-size:6.6px;font-weight:700;margin-bottom:6px;line-height:1.15}
  .col ul{list-style:none}
  .col li{position:relative;padding-left:5px;margin-bottom:3.5px}
  .col li::before{content:"";position:absolute;left:0;top:2.5px;width:2px;height:2px;border-radius:50%;background:var(--white)}
  .col--hw{left:11px;width:90px}
  .col--hw li{padding-left:16px;margin-bottom:2px}
  .col--hw li::before{left:6px}
  .col--hw .label{margin:6px 0 7px}
  .col--services{left:103px;width:78px;border-left:1px solid var(--white);padding-left:3px;height:190px}
  .col--training{left:184px;width:70px;border-left:1px solid var(--white);padding-left:3px;height:190px}

  /* dna */
  .dna-copy{position:absolute;left:31px;top:255px;width:205px;font-size:6.2px;font-weight:400;line-height:1.25}
  .dna-copy p+p{margin-top:5px}

  /* partners */
  .site-url{position:absolute;left:0;width:256px;text-align:center;font-size:11px;font-weight:700;color:var(--navy-text)}

  /* glass panels */
  .glass{position:absolute;border-radius:14px;background:rgba(150,190,245,.45)}
  .glass h3{font-size:10.5px;font-weight:700;line-height:1.2}
  .savings-list{list-style:none;margin-top:4px;border-left:1px solid var(--white);margin-left:6px;font-size:7.4px;font-weight:300;line-height:1.2}
  .savings-list li{position:relative;padding-left:6px;margin-bottom:3px}
  .savings-list li::before{content:"";position:absolute;left:-2.5px;top:3px;width:4px;height:4px;border-radius:50%;border:1px solid var(--white);background:var(--page-blue)}
  .offer-list{list-style:none;font-size:7.6px;font-weight:300;line-height:1.2;position:absolute;left:0;top:34px}
  .offer-list li{position:absolute;white-space:nowrap}
</style>
</head>
<body>

<!-- Cover -->
<section class="page page--cover">
  <svg class="layer" viewBox="0 0 256 360">
    <polygon points="33,0 256,0 256,140 100,238 33,160" fill="#1b2a16"/>
    <path d="M60,250 Q95,272 125,262 L256,180 L256,140 L100,238 Z" fill="var(--lime)"/>
    <polyline points="8,0 8,150 72,238" fill="none" stroke="var(--deep-blue)" stroke-width="18"/>
    <polyline points="24,0 24,158 95,258" fill="none" stroke="#8fc0f0" stroke-width="12"/>
  </svg>
  <div class="photo" role="img" aria-label="Night photo of glowing green skyscrapers under a dark sky"
       style="left:60px;top:0;width:196px;height:120px;background:radial-gradient(circle at 55% 60%,#8fa84a 0%,#3a4f22 35%,transparent 70%)"></div>
  <span class="brand brand--cover">NexaBRIDGE</span>
  <h1 class="cover-title">Hyper<br>Digitalization</h1>
</section>

<!-- Our Expertise -->
<section class="page page--expertise">
  <svg class="layer" viewBox="0 0 256 360">
    <path d="M0,0 H256 V84 C246,80 236,74 234,62 C232,50 226,46 216,50 L200,56 C190,48 180,42 170,46 C160,50 150,56 140,50 C130,44 118,40 108,46 C98,52 90,58 80,54 C70,50 60,44 50,48 C40,52 28,60 0,50 Z" fill="var(--lime)"/>
  </svg>
  <span class="brand">NexaBRIDGE</span>
  <h2 class="heading" style="top:76px;font-size:14px">Our Expertise,</h2>
  <p class="subheading" style="top:100px">Consulting Strategy</p>
  <div class="copy" style="top:120px;width:180px">
    <p>We know that all customers are in different maturity level of digitalization.</p>
    <p>Our Strategy helps to start simple, low cost and produce big changesWe have a graphic that represents the levels, and we need to show into graph that we can help them to take positive path of optimization</p>
  </div>
  <div class="col col--hw">
    <h4>Hardware &amp; Software for industrial operations</h4>
    <p class="label">Software representatives:</p>
    <ul><li>Avendra</li><li>Protecha Kelvra</li><li>Emberton</li><li>OPC Raylux</li><li>Highmark Data</li></ul>
    <p class="label" style="margin-top:8px">Hardware representatives:</p>
    <ul><li>GreyEdge Automation</li><li>Emberton</li><li>Advantra Computers</li><li>Sestra Comm</li></ul>
  </div>
  <div class="col col--services">
    <h4>Services</h4>
    <ul>
      <li>OT interconnectivity for operations</li><li>HMI &amp; MES Support</li>
      <li>Digital Production Process Optimization</li><li>Migration services</li>
      <li>PLC &amp; PAC Control System Support</li>
      <li>Annual Support &amp; Outsourcing plant Engineers</li>
    </ul>
  </div>
  <div class="col col--training">
    <h4>Training</h4>
    <ul>
      <li>Training center &amp; courses:</li><li>Kelvra OPC</li>
      <li>HMI SCADA Wondrel Inreach</li><li>GreyEdge Fixa, Simplexa, Plantora</li>
      <li>PLC Programming</li><li>IIOT Platforms</li><li>Machine Learning Platforms</li>
    </ul>
  </div>
</section>

<!-- Get to know us -->
<section class="page page--about">
  <svg class="layer" viewBox="0 0 256 360">
    <path d="M0,0 H256 V112 C246,104 232,96 226,84 C220,70 224,60 212,56 C200,52 192,64 180,58 C166,50 150,34 136,44 C124,52 110,58 96,54 C84,50 72,46 60,52 C48,58 36,66 20,56 C12,50 6,46 0,46 Z" fill="var(--lime)"/>
  </svg>
  <span class="brand">NexaBRIDGE</span>
  <h2 class="heading" style="top:116px;font-size:14px">Get to know us</h2>
  <div class="copy" style="top:146px;width:200px;font-size:9.4px">
    <p>We offer high performance technology</p>
    <p>State of the art in techniques with Artificial Intelligence and prototypes for new ways of doing manufacturing</p>
    <p>We play the rol as an Architect for a Digital world into the shopfloor operation at Machine Levels</p>
  </div>
</section>

<!-- Our DNA -->
<section class="page page--dna">
  <svg class="layer" viewBox="0 0 256 360">
    <path d="M0,0 H256 V118 C246,110 236,96 232,82 C228,66 220,54 206,54 C192,54 184,64 170,56 C156,48 142,46 128,52 C114,58 102,64 88,56 C74,48 62,46 50,52 C38,58 24,64 0,58 Z" fill="var(--lime)"/>
  </svg>
  <span class="brand">NexaBRIDGE</span>
  <div class="photo" role="img" aria-label="Glowing blue circuit-board brain illustration"
       style="left:31px;top:80px;width:199px;height:145px;border-radius:30px 40px 4px 4px;background:radial-gradient(circle at 50% 45%,#9fd0ff 0%,#2f6fd8 35%,#0c1f5a 80%)"></div>
  <h2 class="heading" style="top:230px;left:31px;font-size:13px">Our DNA</h2>
  <div class="dna-copy">
    <p>We want all companies to operate in an automated way, to be more efficient and to compete with whoever is globally. We have the knowledge and experience to achieve it.</p>
    <p>Our commitments:<br>Improve the operation of each company individually.<br>Impact the country's competitiveness<br>Support companies to access the highest levels of development, productivity, financing and profitability.</p>
  </div>
</section>

<!-- Partners -->
<section class="page page--partners">
  <svg class="layer" viewBox="0 0 256 360">
    <path d="M0,0 H256 V60 C240,58 228,56 214,50 C200,44 186,50 170,48 C150,46 132,44 116,50 C100,56 80,52 60,50 C40,48 20,56 0,54 Z" fill="var(--lime)"/>
  </svg>
  <span class="brand">NexaBRIDGE</span>
  <p class="site-url" style="top:36px">www.protecha.com</p>
  <div class="photo" role="img" aria-label="Website screenshot of an industrial IoT platform home page with an excavator photo"
       style="left:12px;top:57px;width:237px;height:119px;background:linear-gradient(90deg,#f4f6f4 0%,#e6ebe6 45%,#9aa59a 75%,#c9dcb8 100%);border-top:8px solid #1c1f22"></div>
  <p class="site-url" style="top:202px">www.kelvra.com</p>
  <div class="photo" role="img" aria-label="Website screenshot of a factory connectivity product page with a welding photo"
       style="left:15px;top:218px;width:233px;height:128px;background:linear-gradient(90deg,#141618 0%,#1c1f22 40%,#5b6066 75%,#9aa0a6 100%);border-top:8px solid #f5f5f5"></div>
</section>

<!-- Savings cases -->
<section class="page page--savings">
  <div class="photo" role="img" aria-label="Night city skyline over water with blue glowing computer monitors"
       style="inset:0;background:linear-gradient(180deg,#1d3fb0 0%,#2a5ad8 45%,#16318f 70%,#3a6ee0 100%)"></div>
  <svg class="layer" viewBox="0 0 256 360">
    <path d="M0,0 H256 V122 C248,112 240,96 236,80 C232,66 224,56 210,54 C196,52 186,58 172,54 C158,50 150,44 138,48 C128,52 120,60 106,56 C92,52 82,48 68,52 C54,56 40,62 24,54 C14,50 6,46 0,48 Z" fill="var(--lime)"/>
  </svg>
  <span class="brand">NexaBRIDGE</span>
  <div class="glass" style="left:32px;top:70px;width:211px;height:136px;padding:3px 4px 0 4px">
    <h3 style="text-align:center">Cases of savings cost using<br>our tecnology and services</h3>
    <ul class="savings-list">
      <li>Reduce cost operation in manufacturing in 30%</li>
      <li>Augmented Reality functions, adds 60% of productivity and efficiency at operator levels</li>
      <li>Save 17% in Energy for production</li>
      <li>Zero Unplanned Downtime in machine level</li>
      <li>Optimize consistency in recipes by 10% delivers 32% of cost reduction</li>
      <li>Supply Chain optimization by 1% of the cost of goods</li>
    </ul>
  </div>
</section>

<!-- What we can do -->
<section class="page page--offer">
  <div class="photo" role="img" aria-label="Blue binary code background with city lights and glowing monitors"
       style="inset:0;background:linear-gradient(180deg,#1d3fb0 0%,#2456d0 50%,#16318f 75%,#3a6ee0 100%)"></div>
  <svg class="layer" viewBox="0 0 256 360">
    <path d="M0,0 H256 V118 C246,110 236,98 232,84 C228,70 220,58 206,54 C192,50 180,56 166,52 C152,48 140,44 126,50 C112,56 96,58 80,52 C64,46 48,48 30,52 C18,55 8,54 0,50 Z" fill="var(--lime)"/>
  </svg>
  <span class="brand">NexaBRIDGE</span>
  <div class="glass" style="left:30px;top:53px;width:171px;height:144px;padding:4px 6px">
    <h3>What we can do for the<br>customer in a few words</h3>
    <svg style="position:absolute;left:0;top:0" width="171" height="144" viewBox="0 0 171 144">
      <path d="M24,38 C40,60 42,90 30,112 C26,120 20,126 12,130" fill="none" stroke="var(--white)" stroke-width="1"/>
      <g fill="var(--page-blue)" stroke="var(--white)" stroke-width="1">
        <circle cx="26" cy="41" r="2.4"/><circle cx="34" cy="57" r="2.4"/><circle cx="37" cy="71" r="2.4"/>
        <circle cx="36" cy="88" r="2.4"/><circle cx="28" cy="112" r="2.4"/><circle cx="13" cy="129" r="2.4"/>
      </g>
    </svg>
    <ul class="offer-list">
      <li style="left:30px;top:2px">Efficiency in operation</li>
      <li style="left:39px;top:18px">Production Control</li>
      <li style="left:42px;top:31px">Hyper Digitalization of Thing<br>Optimizing asset usage</li>
      <li style="left:38px;top:53px">Maintenance and predictive<br>of assets risks</li>
      <li style="left:30px;top:75px">Quality Control reducing Cost</li>
      <li style="left:16px;top:86px">Augmented Reality in operation<br>and control</li>
    </ul>
  </div>
</section>

</body>
</html>
```